BOLD & MINIMALIST DESIGN NEEDED

We want a very bold but minimalistic business card design that is impactful and utilizes both sides of the business card. Our current logo is included for your use.

We want bold fonts and good use of negative space. We don't want the logo to overpower the design.

Target Market(s)

Professionals who are building new commercial buildings.

Industry/Entity Type

Construction

Contact Information for Business Card

Name, Title, email, office phone, cell phone, website

Font styles to use
Serif
Sans Serif

Requirements
Must have
• Bold design!

```html
<!DOCTYPE html>
<html lang="en">
<head>
<meta charset="utf-8">
<title>Ridgeway Design + Build – Business Card</title>
<link rel="stylesheet" href="https://fonts.googleapis.com/css2?family=Roboto:wght@400;500;700;900&display=swap">
<style>
  :root {
    --page-bg: #e4e4e4;
    --card-white: #ffffff;
    --brand-green: #7dc242;
    --green-light: #b6dd7e;
    --green-dark: #86c44c;
    --ink: #111111;
    --text-gray: #555555;
    --divider: #c8c8c8;
  }
  * { margin: 0; padding: 0; box-sizing: border-box; }
  html, body {
    width: 1200px; height: 1200px; overflow: hidden;
    background: var(--page-bg);
    font-family: "Roboto", Arial, sans-serif;
  }
  .canvas { position: relative; width: 1200px; height: 1200px; }

  .card {
    position: absolute; left: 250px; width: 700px; height: 400px; overflow: hidden;
  }
  .card--front { top: 160px; background: var(--card-white); }
  .card--back {
    top: 640px;
    background: linear-gradient(45deg, var(--green-dark) 0%, #9fd063 55%, var(--green-light) 100%);
  }

  /* brand name (front) */
  .brand {
    position: absolute; display: flex; align-items: center; gap: 10px;
    color: var(--ink); font-weight: 900; text-transform: uppercase; white-space: nowrap;
  }
  .brand__mark { width: 14px; height: 14px; background: var(--brand-green); flex: none; }
  .card--front .brand { left: 48px; top: 180px; font-size: 19px; letter-spacing: 0.5px; }

  .card--back .brand {
    left: 0; right: 0; top: 178px; justify-content: center; font-size: 34px; letter-spacing: 1px;
  }
  .card--back .brand__mark { width: 22px; height: 22px; background: var(--ink); }

  .divider {
    position: absolute; left: 359px; top: 105px; width: 2px; height: 203px;
    background: linear-gradient(to bottom, transparent, var(--divider) 15%, var(--divider) 85%, transparent);
  }

  .contact { position: absolute; left: 388px; top: 112px; color: var(--text-gray); }
  .contact__name { color: var(--brand-green); font-size: 22px; font-weight: 500; letter-spacing: 0.3px; line-height: 1; }
  .contact__title { color: var(--ink); font-size: 15px; font-weight: 500; margin-top: 8px; }
  .contact__address { font-size: 16px; line-height: 20px; margin-top: 16px; }
  .contact__list { list-style: none; margin-top: 18px; font-size: 16px; line-height: 20px; }
  .contact__list li { display: flex; align-items: center; gap: 12px; }
  .contact__icon { width: 13px; height: 13px; flex: none; fill: var(--ink); }

  .curve { position: absolute; left: 0; bottom: 0; width: 700px; height: 62px; display: block; }
</style>
</head>
<body>
<main class="canvas">

  <section class="card card--front" aria-label="Card front">
    <div class="brand"><span class="brand__mark"></span>Ridgeway Design + Build</div>

    <div class="divider"></div>

    <div class="contact">
      <p class="contact__name">Daniel Reeves</p>
      <p class="contact__title">President</p>
      <p class="contact__address">4120 Cedar Hollow Road<br>Juneau, Alaska 99801</p>
      <ul class="contact__list">
        <li>
          <svg class="contact__icon" viewBox="0 0 24 24" aria-hidden="true"><path d="M6.6 10.8a15.1 15.1 0 0 0 6.6 6.6l2.2-2.2c.3-.3.7-.4 1-.2 1.1.4 2.3.6 3.6.6.6 0 1 .4 1 1V20c0 .6-.4 1-1 1C10.6 21 3 13.4 3 4c0-.6.4-1 1-1h3.5c.6 0 1 .4 1 1 0 1.2.2 2.4.6 3.6.1.3 0 .7-.2 1z"/></svg>
          555-214-7730
        </li>
        <li>
          <svg class="contact__icon" viewBox="0 0 24 24" aria-hidden="true"><path d="M2 5h20v14H2z M4 7v.5l8 5 8-5V7z" fill-rule="evenodd"/></svg>
          info@ridgewaybuild.com
        </li>
        <li>
          <svg class="contact__icon" viewBox="0 0 24 24" aria-hidden="true"><circle cx="12" cy="12" r="10"/><path d="M2 12h20M12 2c3 3 3 17 0 20M12 2c-3 3-3 17 0 20" stroke="#fff" stroke-width="1.6" fill="none"/></svg>
          www.ridgewaybuild.com
        </li>
      </ul>
    </div>

    <svg class="curve" viewBox="0 0 700 62" preserveAspectRatio="none" aria-hidden="true">
      <path d="M0 50 Q350 -18 700 50 L700 62 L0 62 Z" fill="var(--brand-green)"/>
      <path d="M0 56 Q350 -6 700 56 L700 62 L0 62 Z" fill="var(--ink)"/>
    </svg>
  </section>

  <section class="card card--back" aria-label="Card back">
    <div class="brand"><span class="brand__mark"></span>Ridgeway Design + Build</div>
  </section>

</main>
</body>
</html>
```